Business Cards for new orthopaedic surgery practice

My husband and I are starting our own orthopaedic surgery practice. We are looking for a business card that is uniform, but one will have my name/title and the other will have his. You can just create one design with my name on it for now. But when I choose your design as the winning design I will ask that you add another copy with his name/title.

We are looking for classy, simple, elite all in one. We like dark blues/a little gold/yellow. Something that goes with our logo. We want our logo incorporated. Here is all the info you need:
Business name: RV Bone & Vitality Center
Location: 38517 North Willowmere Ave
Maple Harbor, FL 33490
Phone: 954-218-4063
Fax: 954-582-7341
Email: info@myrvbonecare.example

Names: Lydia Vance, M.D.
Board Certified Hand and Upper Extremity Surgeon

Ebo Dansu, M.D.
Board Certified Hip & Knee Replacement/General Orthopaedic Surgeon

Can decide what you want to put on the back. Maybe a slogan:
Grounded in Care. Centered on You

I am just going to upload our logo. The only thing is if we select you as the winning design, the location, and phone numbers may change. We will need your help to update that once fully solidified.

Industry/Entity Type

Medical

Contact Information for Business Card

Colors
0054AA
0677BA
7BADD7
CADEEF
E8F1F8
0094D4
00A9DD
6FCCEA
C7EBF8
E9F6FB

Requirements
Must have
• class, appeal,
Should not have
• We want to air on the side of masculine if we are looking at masculine vs. feminine feel. But we still want it classy, sophisticated, and something we will love

```html
<!DOCTYPE html>
<html lang="en">
<head>
<meta charset="utf-8">
<title>RV Bone &amp; Vitality Center — Business Card</title>
<link rel="stylesheet" href="https://fonts.googleapis.com/css2?family=Cinzel:wght@600;700&family=Arimo:wght@400&display=swap">
<style>
  :root {
    --backdrop: #e4e4e4;
    --card-dark: #393939;
    --card-dark-top: #444444;
    --card-light: #ffffff;
    --gold: #c9a15a;
    --navy: #1f2d52;
    --white: #ffffff;
  }
  * { margin: 0; padding: 0; box-sizing: border-box; }
  html, body { width: 1200px; height: 1200px; overflow: hidden; }
  body {
    background: var(--backdrop);
    position: relative;
    font-family: "Arimo", Arial, sans-serif;
  }
  .card {
    position: absolute;
    left: 264px;
    width: 688px;
    height: 393px;
    overflow: hidden;
  }
  .card--front {
    top: 159px;
    background: linear-gradient(to bottom, var(--card-dark-top) 0, var(--card-dark) 40%);
    color: var(--white);
  }
  .card--back {
    top: 653px;
    background: var(--card-light);
  }

  .front-brand {
    position: absolute;
    left: 46px;
    top: 28px;
    width: 108px;
    height: 108px;
    display: flex;
    align-items: center;
    justify-content: center;
    text-align: center;
  }
  .front-brand__ring {
    position: absolute;
    inset: 0;
    border: 2px solid var(--gold);
    border-radius: 50%;
  }
  .front-brand__name {
    font-family: "Cinzel", Georgia, serif;
    font-weight: 700;
    font-size: 11px;
    line-height: 1.3;
    letter-spacing: 0.06em;
    color: var(--white);
  }

  .doctor {
    position: absolute;
    left: 46px;
    top: 153px;
  }
  .doctor__name {
    font-family: "Cinzel", Georgia, serif;
    font-weight: 700;
    font-size: 23px;
    letter-spacing: 0.02em;
    color: var(--gold);
    line-height: 1.2;
  }
  .doctor__title {
    margin-top: 4px;
    font-size: 15.5px;
    line-height: 20px;
  }
  .address {
    position: absolute;
    left: 46px;
    top: 230px;
    font-size: 15.5px;
    line-height: 21px;
    font-style: normal;
  }
  .contacts {
    position: absolute;
    left: 46px;
    top: 285px;
    list-style: none;
    font-size: 15.5px;
  }
  .contacts li {
    display: flex;
    align-items: center;
    height: 20.5px;
  }
  .contacts svg {
    width: 14px;
    height: 14px;
    margin-right: 12px;
    flex: none;
    fill: var(--gold);
  }

  .front-feature {
    position: absolute;
    left: 344px;
    top: 130px;
    width: 330px;
    height: 240px;
    display: flex;
    align-items: center;
    gap: 16px;
  }
  .front-feature__dot {
    width: 26px;
    height: 26px;
    border-radius: 50%;
    background: var(--white);
    flex: none;
  }
  .front-feature__name {
    font-family: "Cinzel", Georgia, serif;
    font-weight: 700;
    font-size: 36px;
    line-height: 1.15;
    color: var(--white);
  }

  .back-brand {
    position: absolute;
    left: 50%;
    top: 58px;
    width: 236px;
    height: 236px;
    transform: translateX(-50%);
    border: 2px solid var(--gold);
    border-radius: 50%;
    display: flex;
    align-items: center;
    justify-content: center;
    text-align: center;
  }
  .back-brand__name {
    font-family: "Cinzel", Georgia, serif;
    font-weight: 700;
    font-size: 24px;
    line-height: 1.3;
    letter-spacing: 0.04em;
    color: var(--navy);
  }
  .tagline {
    position: absolute;
    left: 0;
    right: 0;
    top: 335px;
    text-align: center;
    font-size: 16px;
    letter-spacing: 0.2em;
    color: var(--navy);
  }
</style>
</head>
<body>

<section class="card card--front" aria-label="Business card front">
  <div class="front-brand">
    <span class="front-brand__ring"></span>
    <span class="front-brand__name">RV Bone &amp;<br>Vitality<br>Center</span>
  </div>

  <div class="doctor">
    <h1 class="doctor__name">LYDIA VANCE, M.D.</h1>
    <p class="doctor__title">Board Certified Hand and<br>Upper Extremity Surgeon</p>
  </div>

  <address class="address">
    38517 North Willowmere Ave<br>Maple Harbor, FL 33490
  </address>

  <ul class="contacts">
    <li>
      <svg viewBox="0 0 16 16" aria-hidden="true"><path d="M3.6 1.2l2.3 2.6-1.3 1.7c.8 2 2.6 3.9 4.7 4.9l1.6-1.3 2.8 2.2-1.4 2.6C7 13.6 2.2 8.8 1.2 3.2z"/></svg>
      954-218-4063
    </li>
    <li>
      <svg viewBox="0 0 16 16" aria-hidden="true"><rect x="4" y="1" width="8" height="5"/><rect x="1" y="6" width="14" height="6" rx="1"/><rect x="4" y="11" width="8" height="4" fill="#fff"/></svg>
      954-582-7341
    </li>
    <li>
      <svg viewBox="0 0 16 16" aria-hidden="true"><path d="M1 3h14v10H1z M2 4l6 5 6-5" stroke="#393939" stroke-width="1"/></svg>
      info@myrvbonecare.example
    </li>
    <li>
      <svg viewBox="0 0 16 16" aria-hidden="true"><circle cx="8" cy="8" r="7"/><path d="M5 4c2 1 1 3 3 3s1 3 3 3M9 13c-1-2 1-3 0-4" stroke="#393939" stroke-width="1.2" fill="none"/></svg>
      www.myrvbonecare.example
    </li>
  </ul>

  <div class="front-feature">
    <span class="front-feature__dot"></span>
    <span class="front-feature__name">RV Bone &amp;<br>Vitality<br>Center</span>
  </div>
</section>

<section class="card card--back" aria-label="Business card back">
  <div class="back-brand">
    <span class="back-brand__name">RV Bone &amp;<br>Vitality<br>Center</span>
  </div>
  <p class="tagline">GROUNDED IN CARE. CENTERED ON YOU</p>
</section>

</body>
</html>
```